Beauty Therapy Web Design

I need a web page design for a small beauty therapy clinic, the owner is currently the only beauty therapist working there.
We require the following pages:
Home
About
Treatments
Nails
Courses
Contact
I will attach the clinics business card, treatment menu and signage so that you get a feeling for the branding colours etc.
This is the first website for the beauty therapist, she would like to attract new clients and also tourists that come in on the cruise ships. The thing that sets her apart from other clinics is that she welcomes texting for appointments.
I have selected refundable because I have never done this before so I don't know what to expect, I have the full intention of going through with it as long as I get a good design.
Feel free to ask for further information
Reason: Project extended as I am away for work and am unable to meet with the owner.
Target Market(s)
Females 18 to 50
Industry/Entity Type
Business
Look and feel

```html
<!DOCTYPE html>
<html lang="en">
<head>
<meta charset="utf-8">
<title>Treatments – Serenne Beauty Therapy</title>
<link href="https://fonts.googleapis.com/css2?family=Carlito:wght@400;700&family=Italianno&display=swap" rel="stylesheet">
<style>
  :root{
    --purple:#6b5799;
    --purple-text:#6a5698;
    --gold:#c09d44;
    --gold-heading:#b89a48;
    --white:#ffffff;
    --rule:#7a68a4;
  }
  *{margin:0;padding:0;box-sizing:border-box}
  html,body{width:1200px;height:1200px;overflow:hidden;background:var(--white)}
  body{position:relative;font-family:"Carlito",Calibri,sans-serif;color:var(--purple-text)}
  .abs{position:absolute}

  .site-header{position:absolute;left:0;top:0;width:1200px;height:203px;background:var(--purple)}
  .brand{left:124px;top:40px;color:var(--gold);font-family:"Carlito",sans-serif;font-weight:400;line-height:1}
  .brand-name{display:block;font-size:58px;letter-spacing:1px}
  .brand-sub{display:block;font-size:28px;letter-spacing:1px;margin-top:6px;padding-bottom:5px;border-bottom:1px solid var(--gold);width:262px}
  .booking-line{right:125px;top:18px;font-family:"Italianno",cursive;font-size:26px;color:var(--gold)}
  .main-nav{right:120px;top:150px;display:flex;gap:0}
  .main-nav a{color:var(--white);text-decoration:none;font-size:20px;padding:4px 12px;line-height:25px;border-radius:10px;margin-left:0}
  .main-nav a.current{background:var(--gold)}

  .section-title{font-family:"Italianno",cursive;color:var(--gold-heading);font-size:40px;font-weight:400;line-height:1}
  .intro{font-size:16.5px;line-height:20px}
  .rule{height:1px;background:var(--rule)}

  .price-card{border:3px solid var(--purple);border-top:none}
  .price-card h3{background:var(--purple);color:var(--gold);font-family:"Italianno",cursive;font-weight:400;font-size:38px;height:40px;line-height:44px;padding-left:4px;margin:0 -3px}
  .price-body{display:flex;font-weight:700;font-size:19px;line-height:25px;padding-top:15px}
  .price-body .names{padding-left:3px;border-right:2px solid var(--purple);padding-bottom:14px}
  .price-body .prices{padding-left:16px}

  .text-booking{left:775px;top:727px;width:291px;height:40px;background:var(--purple);color:var(--white);border-radius:10px;font-size:17px;line-height:40px;text-align:center}

  .site-footer{position:absolute;left:0;top:1137px;width:1200px;height:63px;background:var(--purple);color:var(--white);font-size:13.5px}
  .footer-nav{left:128px;top:25px;display:flex;gap:17px}
  .footer-nav a{color:var(--white);text-decoration:none}
  .footer-nav a.current{color:var(--gold);text-decoration:underline}
  .copyright{right:140px;top:26px}
</style>
</head>
<body>
  <header class="site-header">
    <div class="abs brand"><span class="brand-name">Serenne</span><span class="brand-sub">BEAUTY THERAPY</span></div>
    <div class="abs booking-line">Book Your Treaments, Call or Text: 07 555 0142 / 027 555 0198</div>
    <nav class="abs main-nav">
      <a href="#">Home</a><a href="#">About</a><a href="#">Nails</a><a href="#" class="current">Treatments</a><a href="#">Courses</a><a href="#">Contact</a>
    </nav>
  </header>

  <h1 class="abs section-title" style="left:110px;top:220px">Available Treatments</h1>
  <p class="abs intro" style="left:110px;top:267px">Below is a selection of treatments available at Serenne Beauty Therapy.<br>To book a teatment please call or text 07 555 0142 or 027 555 0198</p>
  <div class="abs rule" style="left:112px;top:328px;width:951px"></div>

  <h2 class="abs section-title" style="left:110px;top:348px">Nails</h2>
  <p class="abs intro" style="left:107px;top:396px">We have a range of nail treatments availble including pedicures and manicures</p>

  <section class="abs price-card" style="left:107px;top:449px;width:295px;height:321px">
    <h3>Pedicure</h3>
    <div class="price-body" style="height:278px">
      <div class="names" style="width:195px">Classic - 45 min<br>Deluxe - 60 min<br>Spa Delux - 75 min<br>(Includes Paraffic Dip )<br>Nail Shape<br>Nail Paint<br>French Polish<br>Sen Citizens Nail Trea-<br>tment (Ladies &amp; Gentl-<br>emen)</div>
      <div class="prices">$45.00<br>$60.00<br>$75.00<br><br>$10.00<br>$10.00<br>$15.00<br>$25.00</div>
    </div>
  </section>

  <section class="abs price-card" style="left:442px;top:449px;width:295px;height:243px">
    <h3>Manicure</h3>
    <div class="price-body" style="height:200px">
      <div class="names" style="width:196px">Classic - 45 min<br>Deluxe - 60 min<br>Spa Delux - 75 min<br>(Includes Paraffic Dip )<br>Nail Shape<br>Nail Paint<br>French Polish</div>
      <div class="prices">$35.00<br>$50.00<br>$60.00<br><br>$10.00<br>$10.00<br>$15.00</div>
    </div>
  </section>

  <section class="abs price-card" style="left:774px;top:449px;width:295px;height:226px">
    <h3>Nail Enhancement</h3>
    <div class="price-body" style="height:183px">
      <div class="names" style="width:196px">Acrylic or Gel Full Set<br>Pink Backfill<br>Pink &amp; White Backfill<br>Acrylic Toe Nails<br>Gel Toe Nails<br>Acrylic Nail Removal</div>
      <div class="prices">$70.00<br>$40.00<br>$50.00<br>$65.00<br>$25.00<br>$40.00</div>
    </div>
  </section>

  <div class="abs text-booking">Book Treatment By Text: 07 555 0142</div>

  <div class="abs rule" style="left:108px;top:805px;width:951px"></div>
  <h2 class="abs section-title" style="left:104px;top:824px">Wax and Massage</h2>
  <p class="abs intro" style="left:101px;top:871px">We offer a variety of waxing and massages for men and women</p>

  <footer class="site-footer">
    <nav class="abs footer-nav"><a href="#">Home</a><a href="#">About</a><a href="#">Nails</a><a href="#" class="current">Treatments</a><a href="#">Courses</a><a href="#">Contact</a></nav>
    <div class="abs copyright">© Copyright Serenne Beauty Therapy 2012</div>
  </footer>
</body>
</html>
```